Emergency Dental Referral Company

I need a brochure to advertise my business to prospective dentists that may want to join or to dentists that may want to use this for their own patients. I also need to advertise this brochure to ER physicians who see many dental emergencies. This brochure is meant to be dual purpose: advertise our company and services to the ER physicians who then hand out the brochures to the dental emergency patients in pain. See our website for further details at www.vellumcrestora.com

I will also be attaching our logo design.

Target Market(s)

Emergency Room physicians and other medical personnel who will distribute these brochures to patients in dental pain and dental emergencies

Industry/Entity Type

Business

Font styles to use
Serif
Sans Serif

Requirements
Must have
• Must be simple! Must have a call to action- inspiration to go to website. Highlight our guarantee that states "If you are not seen by a dentist in 24 hours or less, you will receive your money back. Emphasis on the logo. Must discuss how we find a dentist in your zip code in three easy steps.
• For the color- please make similar to our website of www.vellumcrestora.com
Nice to have
• Would like to state that this service can see patients at any hour of the day.
Should not have
• no contact information besides the URL. www.vellumcrestora.com

```html
<!DOCTYPE html>
<html lang="en">
<head>
<meta charset="utf-8">
<title>Vellum Crestora – Brochure Back</title>
<link rel="stylesheet" href="https://fonts.googleapis.com/css2?family=Oswald:wght@300;700&family=Open+Sans:wght@400;600&family=Arimo:wght@400;700&display=swap">
<style>
  :root {
    --green: #3db54a;
    --grey: #e6e7e8;
    --white: #ffffff;
    --ink: #333333;
    --ink-soft: #4a4a4a;
    --photo-light: #f3f5f6;
    --photo-mid: #dde2e5;
  }
  * { margin: 0; padding: 0; box-sizing: border-box; }
  html, body {
    width: 1200px;
    height: 857px;
    overflow: hidden;
    background: var(--white);
  }
  .brochure {
    position: relative;
    width: 1200px;
    height: 857px;
    overflow: hidden;
  }
  .brochure__shapes {
    position: absolute;
    inset: 0;
    width: 1200px;
    height: 857px;
  }
  .headline {
    position: absolute;
    left: 600px;
    width: 600px;
    text-align: center;
    font-family: "Oswald", sans-serif;
    line-height: 1;
    white-space: nowrap;
  }
  .headline--emergency {
    top: 50px;
    font-size: 46px;
    font-weight: 700;
    color: var(--white);
    letter-spacing: -1px;
  }
  .headline--find {
    top: 104px;
    font-size: 66px;
    font-weight: 300;
    color: var(--ink);
    letter-spacing: -2px;
  }
  .headline--steps {
    top: 182px;
    font-size: 45px;
    font-weight: 700;
    color: var(--white);
    letter-spacing: -2px;
  }
  .headline--steps .dark { color: var(--ink); }
  .guarantee {
    position: absolute;
    top: 241px;
    left: 600px;
    width: 600px;
    text-align: center;
    font-family: "Arimo", sans-serif;
    font-size: 18px;
    line-height: 1.2;
    color: var(--white);
    white-space: nowrap;
  }
  .brand {
    position: absolute;
    display: flex;
    align-items: center;
    justify-content: center;
    gap: 10px;
    font-family: "Arimo", sans-serif;
    font-weight: 700;
    line-height: 1;
    white-space: nowrap;
  }
  .brand__dot { border-radius: 50%; flex: none; }
  .brand--front {
    left: 600px;
    width: 600px;
    top: 768px;
    font-size: 26px;
    color: var(--ink-soft);
  }
  .brand--front .brand__dot { width: 22px; height: 22px; background: var(--green); }
  .brand--back {
    left: 0;
    width: 600px;
    top: 740px;
    font-size: 20px;
    color: var(--white);
  }
  .brand--back .brand__dot { width: 16px; height: 16px; background: var(--white); }
  .web-link {
    position: absolute;
    left: 0;
    width: 600px;
    top: 804px;
    text-align: center;
    font-family: "Open Sans", sans-serif;
    font-size: 13px;
    line-height: 1.2;
    color: var(--white);
  }
</style>
</head>
<body>
  <main class="brochure">
    <svg class="brochure__shapes" viewBox="0 0 1050 743" preserveAspectRatio="none">
      <defs>
        <linearGradient id="photoTone" x1="0" y1="0" x2="1" y2="0">
          <stop offset="0" stop-color="#dde2e5"/>
          <stop offset="0.5" stop-color="#f3f5f6"/>
          <stop offset="1" stop-color="#dde2e5"/>
        </linearGradient>
      </defs>

      <rect class="panel-back" x="0" y="0" width="525" height="743" fill="var(--white)"/>
      <polygon class="panel-back__wedge" points="0,219 262,481 0,743" fill="var(--grey)"/>
      <polygon class="panel-back__wedge" points="525,219 263,481 525,743" fill="var(--grey)"/>
      <polygon class="panel-back__base" points="0,743 262,481 525,743" fill="var(--green)"/>

      <rect class="panel-front__photo" x="525" y="0" width="525" height="743" fill="url(#photoTone)" role="img" aria-label="Photo of two dentists in white coats with stethoscopes"/>
      <polygon class="panel-front__header" points="525,0 1050,0 1050,219 787,481 525,219" fill="var(--green)"/>
      <polygon class="panel-front__base" points="525,743 787,481 1050,743" fill="var(--white)"/>
    </svg>

    <h1 class="headline headline--emergency">YOUR EMERGENCY DENTIST</h1>
    <p class="headline headline--find">FIND A DENTIST IN</p>
    <p class="headline headline--steps">3 EASY <span class="dark">STEPS</span></p>
    <p class="guarantee">GET SEEN WITHIN 24 HOURS OR YOUR MONEY BACK!</p>

    <div class="brand brand--front"><span class="brand__dot"></span>Vellum Crestora</div>

    <div class="brand brand--back"><span class="brand__dot"></span>Vellum Crestora</div>
    <p class="web-link">Find your dentist today at www.vellumcrestora.com</p>
  </main>
</body>
</html>
```